To design a brand identity that is simple and creative with 'Corvane' as the brand name, I like modern simple fonts like helvetica neue, I want to print both sides of the card, I am open to dark front and white back, but the design needs to transfer well to letter heads and email signatures, I am looking for sophisticated and elegant, but open minded about clever and off the wall, I do not do 'boring' Corvane Ventures is the mother company for a small group, specialising in Management & consulting, Software development and construction, we have a high level of integrity, we are transparent and accountable for what we do. my images are provided as a guide only, Im not expecting them to be just copied, Im looking for a creator and passionate thinker, who will put life into their work.

Target Market(s)

usually business minded people who are looking for something different in me, such as leadership, confidence and focus with thinking that is per haps a little outside the box..

Industry/Entity Type

Construction

Requirements
Must have
• clean, minmalistic
Nice to have
• custom logo
Should not have
• boring, traditional

```html
<!DOCTYPE html>
<html lang="en">
<head>
<meta charset="utf-8">
<title>Corvane Ventures – Business Card</title>
<link rel="stylesheet" href="https://fonts.googleapis.com/css2?family=Open+Sans:ital,wght@0,400;0,600;0,700;1,400&display=swap">
<style>
  :root {
    --stage: #e9e9ee;
    --card-dark: #2b2b2d;
    --card-dark-edge: #1c1c1e;
    --card-black: #050505;
    --brand-orange: #ea6a2a;
    --name-gold: #f4b000;
    --text-light: #f2f2f2;
    --text-muted: #8a8a8a;
    --service-coral: #f0505a;
    --accent-orange: #ff9a00;
    --accent-red: #f01c24;
    --accent-purple: #8a3a78;
    --accent-teal: #14a58c;
  }
  * { box-sizing: border-box; margin: 0; padding: 0; }
  html, body { width: 1200px; height: 987px; overflow: hidden; }
  body {
    background: var(--stage);
    font-family: "Open Sans", Arial, sans-serif;
    position: relative;
  }
  .card {
    position: absolute;
    width: 640px;
    height: 366px;
    border-radius: 34px;
    overflow: hidden;
    box-shadow: 0 10px 28px rgba(0,0,0,.18);
  }
  /* Front */
  .card-front {
    left: 280px; top: 90px;
    background: linear-gradient(160deg, var(--card-dark) 0%, var(--card-dark-edge) 100%);
  }
  .colour-strip {
    position: absolute; left: 0; right: 0; bottom: 0; height: 56px;
    background: linear-gradient(90deg, var(--accent-orange) 0%, var(--accent-red) 30%, var(--accent-purple) 70%, var(--accent-teal) 100%);
  }
  .brand-lockup {
    position: absolute; left: 120px; top: 52px;
    display: flex; align-items: center; gap: 16px;
  }
  .brand-dot {
    width: 40px; height: 40px; border-radius: 50%;
    background: var(--brand-orange);
  }
  .brand-name {
    font-weight: 600; font-size: 60px; line-height: 1;
    color: var(--brand-orange);
  }
  .tagline {
    position: absolute; left: 178px; top: 124px;
    font-style: italic; font-size: 18px;
    color: var(--text-muted);
  }
  .holder {
    position: absolute; right: 350px; top: 178px;
    text-align: right; color: var(--text-light);
  }
  .holder-name { font-weight: 700; font-size: 23px; color: var(--name-gold); line-height: 1.25; }
  .holder-title { font-size: 18px; line-height: 1.4; }
  .holder-address { font-size: 16px; line-height: 1.5; }
  .divider {
    position: absolute; left: 303px; top: 196px;
    width: 1px; height: 78px; background: #9a9a9a;
  }
  .contact {
    position: absolute; left: 318px; top: 204px;
    list-style: none; color: var(--text-light); font-size: 17px;
  }
  .contact li { display: flex; align-items: center; gap: 8px; line-height: 30px; }
  .contact svg { width: 16px; height: 16px; flex: none; }
  /* Back */
  .card-back {
    left: 280px; top: 540px;
    background: var(--card-black);
  }
  .back-brand {
    position: absolute; right: 70px; top: 80px;
    display: flex; align-items: center; gap: 14px;
  }
  .back-brand .brand-name { font-size: 54px; }
  .services {
    position: absolute; left: 70px; top: 210px;
    color: var(--service-coral); font-size: 20px; line-height: 1.45;
  }
  .services span::before { content: "\2022"; color: #cfcfcf; margin-right: 4px; }
  .web {
    position: absolute; left: 70px; top: 288px;
    color: var(--text-light); font-size: 20px; letter-spacing: 6px;
  }
</style>
</head>
<body>

<section class="card card-front" aria-label="Business card front">
  <div class="colour-strip" role="img" aria-label="Decorative colour band in orange, red, purple and teal"></div>

  <div class="brand-lockup">
    <span class="brand-dot"></span>
    <span class="brand-name">Corvane</span>
  </div>
  <p class="tagline">...in the creation business.</p>

  <div class="holder">
    <p class="holder-name">Your Name</p>
    <p class="holder-title">Title</p>
    <p class="holder-address">Po Box 412 Perth 6031</p>
  </div>
  <span class="divider"></span>
  <ul class="contact">
    <li>
      <svg viewBox="0 0 16 16" aria-hidden="true"><circle cx="8" cy="8" r="8" fill="var(--name-gold)"/><path d="M5.5 4.2l1.4 1.6-.8 1a5 5 0 0 0 2.6 2.6l1-.8 1.6 1.4-.9 1.3C7.8 11.2 4.8 8.2 4.2 5.1z" fill="#222"/></svg>
      +61 0400 555 172
    </li>
    <li>
      <svg viewBox="0 0 16 16" aria-hidden="true"><rect x="1" y="3" width="14" height="10" rx="1.5" fill="var(--name-gold)"/><path d="M2 4l6 5 6-5" fill="none" stroke="#222" stroke-width="1.3"/></svg>
      Names@corvane.ventures
    </li>
  </ul>
</section>

<section class="card card-back" aria-label="Business card back">
  <div class="back-brand">
    <span class="brand-dot"></span>
    <span class="brand-name">Corvane</span>
  </div>
  <p class="services">
    <span>Management &amp; Consulting</span> <span>Software Development</span><br>
    <span>Construction</span>
  </p>
  <p class="web">www.corvane.com</p>
</section>

</body>
</html>
```